Brief 1.
An Overview / Background of the Business & Services-
It is a new business being set up. Our business is to design a solution to enable Alumni of higher institutions in Nigeria apply for their academic transcript through our system. the name of our product will be Record Relay Nigeria. We need logo, site banner, advert banner and several academic images. See www.rrly-ng.example for more insight.
The Target Market / Audience you are trying to reach-
Alumni of Nigeria Universities, usually between the ages of 20-40.
Design Specifics; any preferences or ideas for Style, Colour, Imagery, etc-
Color scheme will be several shades of light blue and white. Please check www.rrly-ng.example for more insight.

Brief 2

Pantrybasket.com is an online food and grocery shop, we supply fresh food stuff and other daily essential needs on request to customers. The site is already up (www.pantrybasket.example). We need logo, site rolling banner, advert banner and several offer graphics as shown in the placeholder images in the site now.
Working women in Nigeria.
Color scheme will be several shades of light Green and White. Please check the site.

```html
<!DOCTYPE html>
<html lang="en">
<head>
<meta charset="utf-8">
<title>Pantry Basket – Feed well, live well</title>
<link rel="stylesheet" href="https://fonts.googleapis.com/css2?family=Open+Sans:wght@400;600;700&display=swap">
<style>
:root{
  --teal:#45bfae;
  --teal-dark:#3aa99a;
  --green:#8dc63f;
  --green-dark:#6fa52a;
  --ink:#2f2f2f;
  --text:#555;
  --muted:#888;
  --line:#e3e3e3;
  --footer:#3b3b3b;
  --footer-base:#262626;
  --white:#fff;
}
*{box-sizing:border-box;margin:0;padding:0}
html,body{width:1200px;height:2244px;overflow:hidden}
body{font-family:"Open Sans",Arial,sans-serif;color:var(--text);background:var(--white);position:relative}
.abs{position:absolute}
a{color:inherit;text-decoration:none}

/* header */
.brand-dot{left:102px;top:24px;width:90px;height:90px;border-radius:50%;background:var(--green)}
.brand-name{left:203px;top:38px;font-size:40px;font-weight:600;color:var(--teal);line-height:1}
.brand-tag{left:205px;top:87px;font-size:13px;color:var(--muted)}
.top-links{right:100px;top:31px;font-size:13px;color:#666;letter-spacing:.2px}
.top-links span.sep{margin:0 8px;color:#aaa}
.cart-sum{left:760px;top:74px;text-align:right;width:60px;font-size:13px;line-height:16px}
.cart-sum .n{color:var(--teal)}
.cart-sum .p{color:#666;font-size:12px}
.cart-btn{left:830px;top:72px;width:32px;height:34px;background:var(--teal)}
.search{left:880px;top:72px;width:179px;height:34px;background:#eef3dc;font-size:14px;color:#777;padding:8px 14px}
.search-btn{left:1059px;top:72px;width:41px;height:34px;background:var(--green)}

/* nav */
.nav{left:0;top:147px;width:1200px;height:48px;background:var(--teal)}
.nav-item{top:147px;height:48px;line-height:48px;font-size:15.5px;font-weight:600;color:var(--white)}
.nav-home{left:100px;width:89px;text-align:center;background:var(--green)}

/* hero */
.hero{left:0;top:195px;width:1200px;height:459px;background:linear-gradient(90deg,#f1f1f1 0%,#e9e9e9 40%,#d9d4cc 70%,#cfcac2 100%)}
.hero-arrow{top:389px;width:55px;height:72px;background:rgba(150,150,150,.75)}
.hero-caption{left:100px;top:531px;width:249px;height:49px;background:rgba(40,40,40,.85);color:var(--white);font-size:29px;line-height:49px;padding-left:13px}
.hero-sub{left:100px;top:586px;width:186px;height:39px;background:var(--teal);color:var(--white);font-size:17px;line-height:39px;padding-left:13px}
.promo-dark{left:797px;top:211px;width:303px;height:172px;background:#2b2b2b;color:var(--white);padding:14px 18px}
.promo-green{left:797px;top:389px;width:303px;height:241px;background:var(--green);padding:16px 18px;color:#2a2a2a}
.promo-title{font-size:25px;font-weight:700;line-height:30px}
.promo-green .promo-title{font-size:29px;line-height:33px}
.promo-text{font-size:16px;margin-top:8px}
.btn-read{display:inline-block;margin-top:14px;padding:4px 10px;font-size:12px;font-weight:600;color:var(--white);border-radius:4px}
.promo-dark .btn-read{background:var(--green)}
.promo-green .btn-read{background:#2b2b2b}
.herb-art{left:1010px;top:548px;width:70px;height:72px;border-radius:8px;background:linear-gradient(#5f8f2a,#3d3d3d)}

/* sidebar */
.side-title{font-size:25px;color:var(--teal)}
.side-rule{height:4px;background:var(--teal)}
.cat{left:100px;width:240px;height:37px;border-bottom:1px solid var(--line);font-size:15px;line-height:37px;padding-left:14px;color:#666}
.cat .caret{position:absolute;right:10px;top:16px;width:0;height:0;border-left:6px solid transparent;border-right:6px solid transparent;border-top:6px solid #bbb}
.side-btn{left:100px;width:240px;height:43px;background:var(--green);color:var(--white);font-size:21px;line-height:43px;padding-left:48px}
.side-btn svg{position:absolute;left:15px;top:12px}
.offer{left:100px;top:1141px;width:240px;height:243px;background:linear-gradient(160deg,#d9d3c4 0%,#8e8778 45%,#2c3a52 100%)}
.offer-badge{left:100px;top:1141px;width:52px;height:48px;background:#f3e9c9;color:#d23c2c;font-weight:700;font-style:normal;font-size:20px;line-height:48px;text-align:center}
.offer-text{left:118px;top:1306px;color:var(--white);font-size:31px;line-height:33px}
.mini{left:100px;width:240px;border-bottom:1px solid var(--line)}
.mini-img{position:absolute;left:0;width:66px;height:58px}
.mini-name{position:absolute;left:78px;font-size:14px;color:#333}
.mini-price{position:absolute;left:78px;font-size:12px;color:var(--teal-dark)}

/* main */
.sec-title{left:361px;font-size:25px;color:var(--ink)}
.sec-arrow{width:24px;height:33px;background:#ddd}
.prod-img{width:240px;height:139px}
.prod-name{width:240px;text-align:center;font-size:14.5px;color:#333}
.prod-price{width:240px;text-align:center;font-size:13px;color:var(--teal-dark)}
.ad{top:950px;height:103px;color:var(--white);padding:8px 12px}
.ad-title{font-size:29px;line-height:34px}
.ad-text{font-size:16.5px;font-weight:700;line-height:22px}
.strip{left:359px;top:1804px;width:741px;height:96px;background:linear-gradient(90deg,#2a2a2a 0%,#121212 45%,#2a2a2a 100%)}
.strip-text{left:612px;top:1815px;font-size:20px;color:var(--white)}
.strip-text b{color:var(--green);font-weight:600;font-size:27px}
.strip-btn{left:883px;top:1850px;width:100px;height:32px;background:var(--green);border-radius:5px;color:var(--white);font-size:12px;font-weight:700;line-height:32px;padding-left:26px}

/* footer */
.footer{left:0;top:1927px;width:1200px;height:257px;background:linear-gradient(#444,#333)}
.foot-head{top:1960px;font-size:15px;font-weight:600;color:#eee}
.foot-list{top:1996px;font-size:12.5px;line-height:25px;color:#bbb;list-style:none}
.social{top:2109px;width:30px;height:30px;background:#f4f4f4;border-radius:3px}
.card{top:2114px;width:42px;height:24px;background:#f4f4f4;border-radius:2px}
.base{left:0;top:2184px;width:1200px;height:60px;background:var(--footer-base);text-align:center;line-height:60px;font-size:12.5px;color:#999}
</style>
</head>
<body>

<!-- header -->
<div class="abs brand-dot"></div>
<div class="abs brand-name">Pantry Basket</div>
<div class="abs brand-tag">Feed well, live well</div>
<div class="abs top-links">MY ACCOUNT<span class="sep">/</span>MY WISHLIST<span class="sep">/</span>MY CART<span class="sep">/</span>CHECKOUT<span class="sep">/</span>LOG IN</div>
<div class="abs cart-sum"><div class="n">0 items</div><div class="p">$00.00</div></div>
<div class="abs cart-btn"><svg width="32" height="34" viewBox="0 0 32 34"><path d="M8 14h16l-2 10H10z" fill="#fff"/><path d="M11 14l4-6M21 14l-4-6" stroke="#fff" stroke-width="2"/></svg></div>
<div class="abs search">Search</div>
<div class="abs search-btn"><svg width="41" height="34" viewBox="0 0 41 34"><circle cx="19" cy="15" r="6" fill="none" stroke="#fff" stroke-width="2.5"/><path d="M23.5 19.5l5 5" stroke="#fff" stroke-width="3"/></svg></div>

<!-- navigation -->
<div class="abs nav"></div>
<div class="abs nav-item nav-home">HOME</div>
<div class="abs nav-item" style="left:209px">HEALTH &amp; WELLNESS</div>
<div class="abs nav-item" style="left:408px">FRUITS &amp; VEGS</div>
<div class="abs nav-item" style="left:560px">POULTRY, MEAT &amp; FISH</div>
<div class="abs nav-item" style="left:773px">FOOD STUFFS</div>
<div class="abs nav-item" style="left:917px">RECIPES</div>
<div class="abs nav-item" style="left:1017px">OTHERS</div>

<!-- hero slider -->
<div class="abs hero" role="img" aria-label="Photo of a woman eating a fresh salad from a bowl"></div>
<div class="abs hero-arrow" style="left:0"><svg width="55" height="72"><path d="M33 18L20 36l13 18" fill="none" stroke="#fff" stroke-width="2"/></svg></div>
<div class="abs hero-arrow" style="left:1145px"><svg width="55" height="72"><path d="M22 18l13 18-13 18" fill="none" stroke="#fff" stroke-width="2"/></svg></div>
<div class="abs hero-caption">Eat Healty Foods</div>
<div class="abs hero-sub">Cras quis accumsan</div>

<div class="abs promo-dark">
  <div class="promo-title">FREE DELIVETRY &amp;<br>GET 10% DISCOUNT</div>
  <div class="promo-text">Every Registered Users</div>
  <span class="btn-read">Read More</span>
</div>
<svg class="abs" style="left:1018px;top:300px" width="68" height="70" viewBox="0 0 68 70"><path d="M6 24L28 4h34v34L40 62z" fill="#f6b800" transform="rotate(20 34 34)"/><circle cx="50" cy="18" r="4" fill="#2b2b2b"/></svg>

<div class="abs promo-green">
  <div class="promo-title">HERBAL &amp;<br>AYURVEDIC &amp; SPA<br>PRODUCTS</div>
  <div class="promo-text">Aliquam erat volutpat</div>
  <span class="btn-read">Read More</span>
</div>
<div class="abs herb-art" role="img" aria-label="Illustration of a mortar and pestle with herbs"></div>

<!-- sidebar -->
<div class="abs side-title" style="left:100px;top:692px">Categories</div>
<div class="abs side-rule" style="left:100px;top:729px;width:240px"></div>
<div class="abs cat" style="top:741px">All</div>
<div class="abs cat" style="top:778px">Health &amp; Wellness</div>
<div class="abs cat" style="top:816px">Fruits &amp; Vegs<span class="caret"></span></div>
<div class="abs cat" style="top:853px">Poultry, Meat &amp; Fish<span class="caret"></span></div>
<div class="abs cat" style="top:891px">Food Stuffs<span class="caret"></span></div>
<div class="abs cat" style="top:928px">Recipes</div>
<div class="abs cat" style="top:966px">Others<span class="caret"></span></div>

<div class="abs side-btn" style="top:1034px"><svg width="24" height="20" viewBox="0 0 24 20"><path d="M2 8h20l-3 10H5z" fill="#fff"/><path d="M6 8l5-6M18 8l-5-6" stroke="#fff" stroke-width="2"/></svg>My Cart - 0 items</div>
<div class="abs side-btn" style="top:1088px"><svg width="24" height="20" viewBox="0 0 24 20"><rect x="2" y="10" width="4" height="9" fill="#fff"/><rect x="9" y="4" width="4" height="15" fill="#fff"/><rect x="16" y="12" width="4" height="7" fill="#fff"/></svg>Compare Products</div>

<div class="abs offer" role="img" aria-label="Photo of a shopper carrying a basket of groceries in a store aisle"></div>
<div class="abs offer-badge">50%</div>
<div class="abs offer-text">Hurry offer<br><span style="padding-left:42px">ends soon</span></div>

<div class="abs side-title" style="left:100px;top:1413px">Latest Products</div>
<div class="abs side-rule" style="left:100px;top:1449px;width:240px"></div>
<div class="abs mini" style="top:1474px;height:77px">
  <div class="mini-img" style="top:0;background:linear-gradient(135deg,#e58a8a,#c85a5a)" role="img" aria-label="Photo of red snapper fillets"></div>
  <div class="mini-name" style="top:2px">Red Snapper (1kg)</div>
  <div class="mini-price" style="top:22px">$1,000.00</div>
  <svg class="abs" style="left:78px;top:40px" width="20" height="18" viewBox="0 0 20 18"><path d="M1 7h18l-3 10H4z" fill="#444"/><path d="M5 7l4-5M15 7l-4-5" stroke="#444" stroke-width="2"/></svg>
</div>
<div class="abs mini" style="top:1571px;height:79px">
  <div class="mini-img" style="top:0;background:linear-gradient(135deg,#eef0f2,#9aa3ab)" role="img" aria-label="Photo of a whole red snapper"></div>
  <div class="mini-name" style="top:2px">Red Snapper (1kg)</div>
  <div class="mini-price" style="top:22px">$1,000.00</div>
  <svg class="abs" style="left:78px;top:40px" width="20" height="18" viewBox="0 0 20 18"><path d="M1 7h18l-3 10H4z" fill="#444"/><path d="M5 7l4-5M15 7l-4-5" stroke="#444" stroke-width="2"/></svg>
</div>

<!-- latest products -->
<div class="abs sec-title" style="top:692px">Latest Products</div>
<div class="abs sec-arrow" style="left:1076px;top:691px"><svg width="24" height="33"><path d="M9 10l7 6.5-7 6.5z" fill="#fff"/></svg></div>

<div class="abs prod-img" style="left:362px;top:730px;background:linear-gradient(135deg,#3b4a66,#1f2638 60%,#4b5b3a)" role="img" aria-label="Photo of fresh blueberries"></div>
<div class="abs prod-img" style="left:612px;top:730px;background:linear-gradient(135deg,#c67a2a,#4d7d2a 55%,#a42a2a)" role="img" aria-label="Photo of a basket of mixed vegetables"></div>
<div class="abs prod-img" style="left:860px;top:730px;background:linear-gradient(135deg,#e7e4de,#a8a9a6 55%,#7a6e62)" role="img" aria-label="Photo of a whole fish on a wooden board"></div>
<div class="abs prod-name" style="left:362px;top:883px">Cras accumsan felis</div><div class="abs prod-price" style="left:362px;top:905px">$1,000.00</div>
<div class="abs prod-name" style="left:612px;top:883px">Cras accumsan felis</div><div class="abs prod-price" style="left:612px;top:905px">$1,000.00</div>
<div class="abs prod-name" style="left:860px;top:883px">Cras accumsan felis</div><div class="abs prod-price" style="left:860px;top:905px">$1,000.00</div>

<div class="abs ad" style="left:361px;width:365px;background:linear-gradient(90deg,#6d6d6d,#8a8a8a 60%,#5d5d5d)" role="img" aria-label="Photo of a delivery man carrying a parcel">
  <div class="ad-title">Free Shipping</div>
  <div class="ad-text">On order over $30 offer today</div>
</div>
<div class="abs ad" style="left:735px;width:365px;background:linear-gradient(90deg,#4f8f1e,#7fb63a 60%,#caa25a)" role="img" aria-label="Photo of a smiling woman talking on the phone">
  <div class="ad-title">Give us call</div>
  <div class="ad-text">1-800-Pantrys<br>(1-800-726-8797)</div>
</div>

<!-- featured products -->
<div class="abs sec-title" style="top:1086px">Featured Products</div>
<div class="abs sec-arrow" style="left:1076px;top:1085px"><svg width="24" height="33"><path d="M9 10l7 6.5-7 6.5z" fill="#fff"/></svg></div>

<div class="abs prod-img" style="left:362px;top:1140px;background:linear-gradient(135deg,#2a1a12,#8a3f1f 55%,#3a2a1a)" role="img" aria-label="Photo of grilled steaks"></div>
<div class="abs prod-img" style="left:612px;top:1140px;background:linear-gradient(135deg,#1e1e1e,#b4581a 55%,#2a2a2a)" role="img" aria-label="Photo of pasta on a fork"></div>
<div class="abs prod-img" style="left:860px;top:1140px;background:linear-gradient(135deg,#6a6a66,#5f8c3a 55%,#8a8a84)" role="img" aria-label="Photo of a bundle of green asparagus"></div>
<div class="abs prod-name" style="left:362px;top:1293px">Cras accumsan felis</div><div class="abs prod-price" style="left:362px;top:1313px">$1,000.00</div>
<div class="abs prod-name" style="left:612px;top:1293px">Cras accumsan felis</div><div class="abs prod-price" style="left:612px;top:1313px">$1,000.00</div>
<div class="abs prod-name" style="left:860px;top:1293px">Cras accumsan felis</div><div class="abs prod-price" style="left:860px;top:1313px">$1,000.00</div>

<div class="abs prod-img" style="left:362px;top:1360px;background:linear-gradient(135deg,#f4f1ea,#c6923a 50%,#6d8a3a)" role="img" aria-label="Photo of assorted groceries and produce"></div>
<div class="abs prod-img" style="left:612px;top:1360px;background:linear-gradient(135deg,#8a5a3a,#c0202a 50%,#3a2a5a)" role="img" aria-label="Photo of strawberries and berries on wood"></div>
<div class="abs prod-img" style="left:860px;top:1360px;background:linear-gradient(135deg,#b8321e,#d2681e 50%,#4f7a2a)" role="img" aria-label="Photo of tomatoes, carrots and greens in a basket"></div>
<div class="abs prod-name" style="left:362px;top:1512px">Cras accumsan felis</div><div class="abs prod-price" style="left:362px;top:1533px">$1,000.00</div>
<div class="abs prod-name" style="left:612px;top:1512px">Cras accumsan felis</div><div class="abs prod-price" style="left:612px;top:1533px">$1,000.00</div>
<div class="abs prod-name" style="left:860px;top:1512px">Cras accumsan felis</div><div class="abs prod-price" style="left:860px;top:1533px">$1,000.00</div>

<div class="abs prod-img" style="left:362px;top:1578px;background:linear-gradient(135deg,#f3f3f3,#8c949a 55%,#dfe3e5)" role="img" aria-label="Photo of whole fish with lemon"></div>
<div class="abs prod-img" style="left:612px;top:1578px;background:linear-gradient(135deg,#6a4a30,#e0703a 50%,#4a3424)" role="img" aria-label="Photo of salmon fillet on a board"></div>
<div class="abs prod-img" style="left:860px;top:1578px;background:linear-gradient(135deg,#e8d6b0,#c2461e 50%,#f2ece2)" role="img" aria-label="Photo of grilled prawn skewers"></div>
<div class="abs prod-name" style="left:362px;top:1732px">Cras accumsan felis</div><div class="abs prod-price" style="left:362px;top:1753px">$1,000.00</div>
<div class="abs prod-name" style="left:612px;top:1732px">Cras accumsan felis</div><div class="abs prod-price" style="left:612px;top:1753px">$1,000.00</div>
<div class="abs prod-name" style="left:860px;top:1732px">Cras accumsan felis</div><div class="abs prod-price" style="left:860px;top:1753px">$1,000.00</div>

<div class="abs strip" role="img" aria-label="Photo of plated dishes and salmon on a dark table"></div>
<div class="abs strip-text">Phasellus et <b>pulvinar</b> tellus accumsan.</div>
<div class="abs strip-btn"><svg class="abs" style="left:8px;top:9px" width="14" height="14"><circle cx="7" cy="7" r="6" fill="#fff"/><path d="M5.5 4l3.5 3-3.5 3z" fill="#6fa52a"/></svg>Learn More</div>

<!-- footer -->
<div class="abs footer"></div>
<div class="abs foot-head" style="left:130px">Navigation Menu</div>
<ul class="abs foot-list" style="left:130px"><li>All</li><li>Health &amp; Wellness</li><li>Fruits &amp; Vegs</li><li>Poultry, Meat &amp; Fish</li></ul>
<ul class="abs foot-list" style="left:277px"><li>Food Stuffs</li><li>Recipes</li><li>Others</li></ul>
<div class="abs foot-head" style="left:422px">Customer Service</div>
<ul class="abs foot-list" style="left:422px"><li>About Us</li><li>Delivery Information</li><li>Privacy Policy</li><li>Term &amp; Condition</li></ul>
<div class="abs foot-head" style="left:726px">My Account</div>
<ul class="abs foot-list" style="left:726px"><li>My Product</li><li>My Orders</li><li>My Address</li><li>My Personal Info</li></ul>
<div class="abs foot-head" style="left:956px">Other Links</div>
<ul class="abs foot-list" style="left:956px"><li>Site Map</li><li>Search Terms</li><li>Advanced Search</li><li>Orders and Returns</li><li>Contact Us</li></ul>

<div class="abs social" style="left:133px"></div>
<div class="abs social" style="left:167px"></div>
<div class="abs social" style="left:201px"></div>
<div class="abs social" style="left:235px"></div>
<div class="abs social" style="left:269px"></div>

<div class="abs card" style="left:424px"></div>
<div class="abs card" style="left:475px"></div>
<div class="abs card" style="left:532px"></div>
<div class="abs card" style="left:587px"></div>

<div class="abs base">Copyright &copy; 2014 Pantrybasket.com Ltd.&nbsp;&nbsp;&nbsp;All rights reserved.</div>

</body>
</html>
```